Deisgn A Manual Cover for an Australian Health Training Company

We are looking for an A4 Front of Manual Cover Design for a comprehensive administrative training manual to be launched soon in Australia.

The title of the book is :

"Drafting, Shaping and Shipping Office Paperwork"

for the Australian Medical Office (smaller font)

Written and compiled by Mel Dobrik

Target Market(s)

25-45 year old medical administrative students (usually female)

Industry/Entity Type

It Company

Font styles to use
Serif

Colors
3176b5
f68d4c
33b8a4
fffbf0

Requirements
Must have
• University like perhaps
• Human element (picture/s of people)
• About the concept of designing and producing documents in a health setting (this can be entirely conceptual).
• Conceptual design would be considered
• Appealing

```html
<!DOCTYPE html>
<html lang="en">
<head>
<meta charset="UTF-8">
<title>Drafting, Shaping and Shipping Office Paperwork – Manual Cover</title>
<link rel="stylesheet" href="https://fonts.googleapis.com/css2?family=Cinzel:wght@400;500&family=Questrial&display=swap">
<style>
  :root {
    --backdrop: #7f9fae;
    --backdrop-dark: #5f8193;
    --paper: #ffffff;
    --ink-blue: #3176b5;
    --accent-orange: #f68d4c;
    --accent-teal: #33b8a4;
    --cream: #fffbf0;
    --photo-light: #e4eef5;
    --photo-mid: #b9cddd;
    --photo-warm: #d9c4b4;
  }
  * { box-sizing: border-box; margin: 0; padding: 0; }
  html, body {
    width: 1200px;
    height: 784px;
    overflow: hidden;
  }
  body {
    background: radial-gradient(ellipse at 45% 40%, var(--backdrop) 0%, var(--backdrop-dark) 100%);
    display: flex;
    align-items: center;
    justify-content: center;
  }
  .manual-cover {
    position: relative;
    width: 520px;
    height: 736px;
    background: var(--paper);
    box-shadow: 0 18px 40px rgba(30, 50, 60, 0.35);
    display: flex;
    flex-direction: column;
    align-items: center;
  }
  .college-mark {
    margin-top: 34px;
    display: flex;
    flex-direction: column;
    align-items: center;
    gap: 4px;
  }
  .college-name {
    display: flex;
    align-items: center;
    gap: 7px;
    font-family: "Cinzel", serif;
    font-weight: 500;
    font-size: 11px;
    letter-spacing: 0.06em;
    color: var(--ink-blue);
  }
  .college-name .mark-square {
    width: 11px;
    height: 11px;
    background: var(--ink-blue);
  }
  .college-tagline {
    font-family: "Cinzel", serif;
    font-size: 6px;
    letter-spacing: 0.08em;
    color: var(--ink-blue);
  }
  .manual-title {
    margin-top: 26px;
    font-family: "Cinzel", serif;
    font-weight: 400;
    font-size: 46px;
    line-height: 47px;
    color: var(--ink-blue);
    text-align: center;
    letter-spacing: 0.01em;
  }
  .manual-title span { display: block; }
  .manual-subtitle {
    margin-top: 8px;
    width: 400px;
    display: flex;
    align-items: center;
    gap: 8px;
    font-family: "Questrial", sans-serif;
    font-size: 11px;
    letter-spacing: 0.06em;
    color: var(--accent-orange);
    white-space: nowrap;
  }
  .manual-subtitle::before,
  .manual-subtitle::after {
    content: "";
    flex: 1;
    height: 1px;
    background: var(--accent-orange);
  }
  .cover-photo {
    margin-top: 10px;
    width: 440px;
    height: 216px;
    background:
      radial-gradient(ellipse 70px 110px at 22% 55%, var(--photo-warm) 0%, transparent 75%),
      radial-gradient(ellipse 60px 90px at 62% 60%, var(--photo-mid) 0%, transparent 80%),
      linear-gradient(120deg, var(--photo-light) 0%, #cfdde8 60%, var(--photo-mid) 100%);
  }
  .author-band {
    width: 440px;
  }
  .author-label {
    background: var(--accent-orange);
    color: var(--cream);
    font-family: "Questrial", sans-serif;
    font-size: 11px;
    letter-spacing: 0.08em;
    text-align: center;
    padding: 3px 0 2px;
  }
  .author-name {
    background: var(--accent-teal);
    color: var(--paper);
    font-family: "Questrial", sans-serif;
    font-size: 46px;
    letter-spacing: 0.05em;
    text-align: center;
    height: 76px;
    line-height: 76px;
  }
</style>
</head>
<body>
  <main class="manual-cover">
    <header class="college-mark">
      <div class="college-name"><span class="mark-square"></span>Harbourline College of Training</div>
      <div class="college-tagline">Building Skills | Shaping Careers</div>
    </header>

    <h1 class="manual-title">
      <span>Drafting,</span>
      <span>Shaping</span>
      <span>&amp; Shipping</span>
      <span>Office</span>
      <span>Paperwork</span>
    </h1>

    <p class="manual-subtitle">FOR THE AUSTRALIAN MEDICAL OFFICE</p>

    <div class="cover-photo" role="img" aria-label="Photo of a smiling medical professional with a stethoscope, with a doctor and a child softly blurred in a bright clinic behind her"></div>

    <footer class="author-band">
      <div class="author-label">WRITTEN AND COMPILED BY</div>
      <div class="author-name">MEL DOBRIK</div>
    </footer>
  </main>
</body>
</html>
```